Retail Jewelry Business Card Design Project

We are in need of a new business card design for a retail jewelry store. This store is in the business of fine jewelry including but not specific to bridal jewelry, diamonds, designer jewelry and watches.

This store has been in business for 20 years but continues to strive for a modern professional appeal. The main colors use for this business are a royal blue, white and silver.

Target Market(s)

Target market is ages 18-50

Industry/Entity Type

Jewelry

Requirements
Must have
• Sales Person Name
Sales Person Email Address

Store Address
Store Phone
Website

Standard business card size. No odd shapes or sizes.
Nice to have
• Overall modern feel for card.

We have thought that a design with a nice feature of the logo on the back of the card would be nice but open to ideas.
Should not have
• No specific images of jewelry should be used.

```html
<!DOCTYPE html>
<html lang="en">
<head>
<meta charset="utf-8">
<title>Marlow Avery Fine Jewelry – Business Card</title>
<link rel="stylesheet" href="https://fonts.googleapis.com/css2?family=Cormorant+Garamond:wght@500&display=swap">
<style>
  :root {
    --page: #e9e7e3;
    --card-deep: #0b0b0c;
    --card-mid: #1c1c1e;
    --silver: #d9dadc;
    --silver-soft: #a9abaf;
    --rule: rgba(217, 218, 220, 0.55);
  }
  * { box-sizing: border-box; margin: 0; padding: 0; }
  html, body {
    width: 1200px; height: 1024px; overflow: hidden;
    background: var(--page);
    font-family: "Cormorant Garamond", Georgia, serif;
    font-weight: 500;
    color: var(--silver);
  }
  .sheet {
    width: 1200px; height: 1024px;
    display: flex; flex-direction: column; align-items: center; justify-content: center;
    gap: 60px;
  }
  .card {
    position: relative;
    width: 700px; height: 400px;
    border-radius: 4px;
    overflow: hidden;
    box-shadow: 0 12px 30px rgba(0,0,0,0.28);
  }
  .card-pattern {
    position: absolute; inset: 0;
    background: radial-gradient(ellipse at 40% 30%, var(--card-mid) 0%, var(--card-deep) 75%);
  }
  .card-content { position: relative; height: 100%; }

  .brand { display: flex; align-items: center; gap: 14px; line-height: 1; }
  .brand-dot { width: 12px; height: 12px; border-radius: 50%; background: var(--silver); flex: none; }
  .brand-name { font-size: 50px; color: var(--silver); }
  .brand-name small { display: block; font-size: 20px; letter-spacing: 0.32em; margin-top: 8px; text-transform: uppercase; }

  /* Front */
  .card-front .card-content { padding: 38px 44px; }
  .card-front .brand { margin-bottom: 20px; }
  .contact-list { list-style: none; }
  .contact-row {
    display: flex; align-items: center; gap: 22px;
    font-size: 22px; padding: 13px 0;
    border-top: 1px solid var(--rule);
  }
  .contact-item { display: flex; align-items: center; gap: 10px; }
  .icon { width: 16px; height: 16px; fill: var(--silver); flex: none; }

  /* Back */
  .card-back .card-content {
    display: flex; flex-direction: column; align-items: center; justify-content: center; gap: 30px;
  }
  .card-back .brand-name { font-size: 64px; text-align: center; }
  .card-back .brand-name small { font-size: 24px; border-top: 1px solid var(--rule); padding-top: 10px; }
  .back-url { font-size: 24px; color: var(--silver-soft); }
</style>
</head>
<body>
<main class="sheet">

  <section class="card card-front">
    <div class="card-pattern" role="img" aria-label="Dark floral damask pattern across the card"></div>
    <div class="card-content">
      <div class="brand">
        <div class="brand-name">Marlow Avery<small>Fine Jewelry</small></div>
        <span class="brand-dot"></span>
      </div>
      <ul class="contact-list">
        <li class="contact-row">
          <span class="contact-item">
            <svg class="icon" viewBox="0 0 16 16"><circle cx="8" cy="4.5" r="3.5"/><path d="M1 16c0-4 3-6.5 7-6.5s7 2.5 7 6.5z"/></svg>
            Marlow Avery Lindqvist
          </span>
        </li>
        <li class="contact-row">
          <span class="contact-item">
            <svg class="icon" viewBox="0 0 16 16"><path d="M8 0a5.5 5.5 0 0 0-5.5 5.5C2.5 10 8 16 8 16s5.5-6 5.5-10.5A5.5 5.5 0 0 0 8 0zm0 7.8a2.3 2.3 0 1 1 0-4.6 2.3 2.3 0 0 1 0 4.6z"/></svg>
            418 Beacon Avenue Port Lorel, FL 32999
          </span>
        </li>
        <li class="contact-row">
          <span class="contact-item">
            <svg class="icon" viewBox="0 0 16 16"><path d="M3.6 0.8 6 3.6 4.6 5.6c.9 2.1 3.4 4.7 5.8 5.8l2-1.4 2.8 2.4-1.6 2.6C7.6 15 1 8.4 1 2.4z"/></svg>
            000-000-0000
          </span>
          <span class="contact-item">
            <svg class="icon" viewBox="0 0 16 16"><path d="M0 3h16v1.2L8 9 0 4.2z"/><path d="M0 5.6 8 10.4l8-4.8V13H0z"/></svg>
            marlow@marlowaveryjewelry.com
          </span>
        </li>
        <li class="contact-row">
          <span class="contact-item">
            <svg class="icon" viewBox="0 0 16 16"><path d="M8 0a8 8 0 1 0 0 16A8 8 0 0 0 8 0zm0 1.5c.9 0 2 1.6 2.4 4.5H5.6C6 3.1 7.1 1.5 8 1.5zM5.5 7.5h5a14 14 0 0 1 0 1H5.5a14 14 0 0 1 0-1zM1.6 7.5h2.4v1H1.6zm10.4 0h2.4v1H12zM5.6 10h4.8C10 12.9 8.9 14.5 8 14.5S6 12.9 5.6 10z"/></svg>
            www.marlowaveryjewelry.com
          </span>
        </li>
      </ul>
    </div>
  </section>

  <section class="card card-back">
    <div class="card-pattern" role="img" aria-label="Dark floral damask pattern across the card"></div>
    <div class="card-content">
      <div class="brand">
        <span class="brand-dot"></span>
        <div class="brand-name">Marlow Avery<small>Fine Jewelry</small></div>
      </div>
      <p class="back-url">www.marlowaveryjewelry.com</p>
    </div>
  </section>

</main>
</body>
</html>
```